uk based ecommerce website requires fresh look ,high quality look and feel

we are a web based company selling eco friendly ground reinforcement grids to diy and construction sectors
our existing website is www.pondermeshpaths.co.uk ,

we have already updated the logo so that is the branding sorted .so we need a ecommerce website that is very much up-to date in design and layout and which has content management system for ease of use so that we can add products and information as required.

Use current logo as reference for colour scheme.
www.pondermeshpaths.co.uk

The current website has 6 pages accessible through the navigation bar, I would now like 5 pages, removing the need for the Trade Enquiries page possibly have it with along with contact us.

Target Market(s)

construction industry , diy end users,
retail market, landscapers, gardeners

Industry/Entity Type

Construction

Font styles to use
Other font styles liked:
• logo font prometo

Colors
f78f20
9bcb3c

Requirements
Must have
• logo colours and logo design in website with cms responsive design for tablet and mobile devices
• expect content to work flawlessly and look great across all devices
• HTML 5 custom design with coding as required
• must have good experiance in ecommerce website design
• eye catching, high quality look and feel and very user friedly ,very up-to date.
Nice to have
• picture slider show
• explain in writing what exactly i am getting in my ecommerce website
Should not have
• plain , basic design , old fashion looking ,cheap look

```html
<!DOCTYPE html>
<html lang="en">
<head>
<meta charset="utf-8">
<title>PonderMesh Ground Solutions</title>
<link href="https://fonts.googleapis.com/css2?family=PT+Sans:wght@400;700&family=Open+Sans:wght@400;600&display=swap" rel="stylesheet">
<style>
:root{
  --orange:#f78f20;
  --green:#9bcb3c;
  --ink:#2b2b2b;
  --text:#555;
  --panel:#f4f4f4;
  --line:#e3e3e3;
  --dark:#2a2a2a;
  --darker:#1f1f1f;
  --blue:#3b5a9a;
  --sky:#2fa3e0;
  --navy:#1f6fa8;
}
*{box-sizing:border-box;margin:0;padding:0}
html,body{width:1200px;height:2525px;overflow:hidden}
body{position:relative;background:#f0f0f0;font-family:"Open Sans",sans-serif;color:var(--text)}
.abs{position:absolute}
h1,h2,h3,h4,.nav,.btn,.tab{font-family:"PT Sans",sans-serif}

.topbar{left:0;top:0;width:1200px;height:5px;background:var(--green)}
.account{right:103px;top:0;display:flex;height:24px;font-size:11px;color:#fff}
.account span{display:flex;align-items:center;padding:0 14px}
.account .login{background:var(--green);border-radius:0 0 0 10px}
.account .register{background:var(--orange);border-radius:0 0 10px 0}

.header{left:0;top:5px;width:1200px;height:150px;background:#fff}
.brand{left:100px;top:40px;display:flex;align-items:center;gap:12px}
.brand-dot{width:52px;height:52px;border-radius:50%;background:var(--orange)}
.brand-name{font-family:"PT Sans",sans-serif;font-weight:700;font-size:25px;line-height:1.05;color:var(--orange)}
.header-contact{right:50px;top:48px;display:flex;align-items:center;gap:8px}
.social{display:flex;gap:8px}
.social i{display:block;width:36px;height:36px;border-radius:50%}
.phone{display:flex;align-items:center;gap:8px;margin-left:10px;color:var(--green);font-size:19px;font-family:"PT Sans",sans-serif;white-space:nowrap}
.phone .ic{width:36px;height:36px;border-radius:50%;background:var(--green);display:flex;align-items:center;justify-content:center}
.nav{right:98px;top:104px;display:flex;gap:26px;font-size:13px;color:#333;align-items:center}
.nav a{text-decoration:none;color:inherit;padding-bottom:6px}
.nav .active{color:var(--orange);border-bottom:2px solid var(--orange)}

.hero{left:0;top:155px;width:1200px;height:513px;background:radial-gradient(circle at 50% 40%,#5c5c5c,#2e2e2e 75%)}
.hero-title{left:0;top:350px;width:1200px;text-align:center;color:#fff;font-size:31px;font-weight:700;letter-spacing:.5px}
.hero-rule{left:382px;top:392px;width:436px;height:2px;background:#fff}
.hero-text{left:310px;top:405px;width:580px;text-align:center;color:#fff;font-size:13px;line-height:22px}
.arrow{top:390px}
.btn{display:inline-flex;align-items:center;justify-content:center;gap:6px;background:var(--orange);color:#fff;border-radius:30px;font-weight:700;font-size:13px}
.hero-btn{left:513px;top:461px;width:174px;height:50px}

.welcome{left:100px;top:602px;width:1000px;height:133px;background:#fff}
.welcome-mark{left:155px;top:624px;width:46px;height:46px;border-radius:50%;background:var(--green)}
.welcome-title{left:212px;top:625px;font-size:29px;color:var(--orange);font-weight:700;white-space:nowrap}
.welcome-rule{left:212px;top:667px;width:730px;height:2px;background:var(--green)}
.welcome-sub{left:313px;top:676px;font-size:16px;color:var(--ink);font-weight:700;letter-spacing:.3px;white-space:nowrap}

.tab{top:735px;width:166px;height:55px;display:flex;align-items:center;justify-content:center;gap:8px;font-size:12px;color:#fff;background:var(--orange)}
.tab.current{background:var(--panel);color:#333;border:1px solid var(--line);border-bottom:none}

.content{left:100px;top:790px;width:1000px;height:1104px;background:var(--panel);border:1px solid var(--line)}
.intro-title{left:124px;top:826px;font-size:18px;color:var(--ink);font-weight:700}
.intro-text{left:124px;top:860px;width:960px;font-size:12px;line-height:21px}

.feature{top:968px;width:460px;height:320px;overflow:hidden}
.feature .photo{position:absolute;inset:0}
.feature .panel{position:absolute;right:0;top:0;width:258px;height:320px;background:var(--orange);clip-path:polygon(16% 0,100% 0,100% 100%,16% 100%,0 50%);padding:55px 20px 0 52px;color:#fff}
.feature h4{font-size:20px;line-height:26px;font-weight:700;margin-bottom:12px}
.feature li{list-style:none;display:flex;align-items:center;gap:7px;font-size:11px;height:25px}
.feature .more{margin-top:16px;background:#fff;color:#333;width:130px;height:40px}

.card{width:216px;height:255px;background:#fff;border:1px solid var(--line);text-align:center}
.card .photo{height:128px}
.card h4{font-size:19px;color:var(--ink);font-weight:700;margin-top:17px;white-space:nowrap}
.card small{display:block;font-size:11px;color:#333;font-family:"PT Sans",sans-serif;font-weight:700;margin-top:1px}
.card .btn{margin-top:10px;width:110px;height:32px;font-size:11px}

.cta{left:0;top:1900px;width:1200px;height:315px;background:linear-gradient(135deg,#3a3a3a,#262626 60%,#333)}
.cta-q{left:0;top:1985px;width:1200px;text-align:center;color:#fff;font-size:17px;font-weight:700;font-family:"PT Sans",sans-serif}
.cta-call{left:0;top:2020px;width:1200px;text-align:center;color:#fff;font-size:30px;font-weight:700;font-family:"PT Sans",sans-serif}
.cta-call span{color:var(--green)}
.cta-btn{left:513px;top:2080px;width:174px;height:50px}

.footer{left:0;top:2215px;width:1200px;height:252px;background:var(--dark);color:#ddd}
.footer-title{color:#fff;font-size:22px;font-weight:700}
.f-row{position:absolute;display:flex;gap:14px;font-size:12px;line-height:20px;color:#ddd}
.field{position:absolute;left:455px;width:265px;height:34px;border-radius:20px;background:#fff;font-size:12px;color:#666;padding:8px 14px}
.submit{left:453px;top:2399px;width:103px;height:32px;font-size:12px}
.tweet{left:780px;top:2328px;width:300px;text-align:center;font-size:12px;line-height:19px;font-style:italic;color:#ddd}
.tweet a{color:var(--green)}
.tweet em{color:var(--orange)}
.bottom{left:0;top:2467px;width:1200px;height:58px;background:var(--darker);color:#ccc;font-size:12px}
.bottom p{position:absolute;left:100px;top:20px}
.bottom .social{position:absolute;right:140px;top:11px}
.bottom .code{position:absolute;right:100px;top:20px}
</style>
</head>
<body>
<div class="abs topbar"></div>
<header class="abs header"></header>
<div class="abs account"><span class="login">Login</span><span class="register">Register</span></div>
<div class="abs brand"><i class="brand-dot"></i><span class="brand-name">PONDERMESH<br>GROUND SOLUTIONS</span></div>
<div class="abs header-contact">
  <div class="social"><i style="background:var(--blue)"></i><i style="background:var(--sky)"></i><i style="background:var(--navy)"></i><i style="background:var(--orange)"></i></div>
  <div class="phone"><span class="ic"><svg width="18" height="18" viewBox="0 0 24 24"><path fill="#fff" d="M6.6 10.8a15 15 0 0 0 6.6 6.6l2.2-2.2c.3-.3.7-.4 1-.2 1.1.4 2.3.6 3.6.6.6 0 1 .4 1 1V20c0 .6-.4 1-1 1A17 17 0 0 1 3 4c0-.6.4-1 1-1h3.5c.6 0 1 .4 1 1 0 1.3.2 2.5.6 3.6.1.3 0 .7-.2 1z"/></svg></span>0845-000-1234</div>
</div>
<nav class="abs nav"><a class="active">HOME</a><a>SHOP</a><a>ABOUT US</a><a>GROUND SOLUTIONS</a><a>PONDERMESH</a><a>CONTACT US</a><svg width="13" height="13" viewBox="0 0 24 24" style="margin-bottom:6px"><circle cx="10" cy="10" r="7" fill="none" stroke="#333" stroke-width="3"/><path d="M15 15l7 7" stroke="#333" stroke-width="3"/></svg></nav>

<div class="abs hero" role="img" aria-label="Close-up of dark gravel held in a black hexagonal grid"></div>
<svg class="abs arrow" style="left:32px" width="16" height="50" viewBox="0 0 16 50"><path d="M14 2L2 25l12 23" fill="none" stroke="#fff" stroke-width="2"/></svg>
<svg class="abs arrow" style="right:32px" width="16" height="50" viewBox="0 0 16 50"><path d="M2 2l12 23L2 48" fill="none" stroke="#fff" stroke-width="2"/></svg>
<h2 class="abs hero-title">PONDERMESH GROUND SOLUTION</h2>
<div class="abs hero-rule"></div>
<p class="abs hero-text">We supply a permeable paving system that keeps the traditional look of a gravel driveway, but gives it the more advanced and ecological approach of a contained gravel system</p>
<span class="abs btn hero-btn">&#9432; MORE INFO</span>

<section class="abs welcome"></section>
<i class="abs welcome-mark"></i>
<h1 class="abs welcome-title">WELCOME TO PONDERMESH GROUND SOLUTION</h1>
<div class="abs welcome-rule"></div>
<h2 class="abs welcome-sub">CONTAINED GRAVEL FOR PARKING AND PATHWAYS</h2>

<div class="abs tab current" style="left:232px">&#9432; CORE PRODUCTS</div>
<div class="abs tab" style="left:422px">&#9874; PRODUCT USE</div>
<div class="abs tab" style="left:612px">&#9654; VIDEOS</div>
<div class="abs tab" style="left:803px">&#9776; LATEST NEWS</div>

<section class="abs content"></section>
<h3 class="abs intro-title">FORDABLE AND GREEN SOLUTIONS FOR FLOOD PREVENTION</h3>
<p class="abs intro-text">PonderMesh is a family run company that specialises in stabilisation grid systems for gravel and grass surfaces. Our main focus is to provide Quality products at an affordable price and which meets the requirements of our customers. We supply a permeable paving system that keeps the traditional look of a gravel driveway, but gives it the more advanced and ecological approach of a contained gravel system All installations of all landscaping of driveways projects require to incorporate the SUDS techniques which is Sustainable Urban Drainage Systems.</p>

<article class="abs feature" style="left:126px">
  <div class="photo" role="img" aria-label="Worker raking gravel into a blue grid on a driveway" style="background:linear-gradient(160deg,#c9b59a,#8a7d6e 50%,#3f5572)"></div>
  <div class="panel"><h4>LIGHT DOMESTIC<br>DRIVEWAYS</h4><ul>
  <li><svg width="11" height="11" viewBox="0 0 12 12"><circle cx="6" cy="6" r="6" fill="#fff"/><path d="M3 6l2 2 4-4" fill="none" stroke="#f78f20" stroke-width="1.6"/></svg>GEOTEXTILE MEMBRANES</li>
  <li><svg width="11" height="11" viewBox="0 0 12 12"><circle cx="6" cy="6" r="6" fill="#fff"/><path d="M3 6l2 2 4-4" fill="none" stroke="#f78f20" stroke-width="1.6"/></svg>LIGHT DOMESTIC DRIVEWAYS</li>
  <li><svg width="11" height="11" viewBox="0 0 12 12"><circle cx="6" cy="6" r="6" fill="#fff"/><path d="M3 6l2 2 4-4" fill="none" stroke="#f78f20" stroke-width="1.6"/></svg>HEAVY DOMESTIC DRIVEWAYS</li>
  <li><svg width="11" height="11" viewBox="0 0 12 12"><circle cx="6" cy="6" r="6" fill="#fff"/><path d="M3 6l2 2 4-4" fill="none" stroke="#f78f20" stroke-width="1.6"/></svg>COMMERCIAL PARKING</li>
  </ul><span class="btn more">&#9432; MORE INFO</span></div>
</article>
<article class="abs feature" style="left:612px">
  <div class="photo" role="img" aria-label="White gravel above a black hexagonal grid" style="background:linear-gradient(180deg,#7f9a6a,#c8c8c4 35%,#8b8b8b 65%,#2c2c2c)"></div>
  <div class="panel"><h4>HEAVY DOMESTIC<br>DRIVEWAYS</h4><ul>
  <li><svg width="11" height="11" viewBox="0 0 12 12"><circle cx="6" cy="6" r="6" fill="#fff"/><path d="M3 6l2 2 4-4" fill="none" stroke="#f78f20" stroke-width="1.6"/></svg>GEOTEXTILE MEMBRANES</li>
  <li><svg width="11" height="11" viewBox="0 0 12 12"><circle cx="6" cy="6" r="6" fill="#fff"/><path d="M3 6l2 2 4-4" fill="none" stroke="#f78f20" stroke-width="1.6"/></svg>LIGHT DOMESTIC DRIVEWAYS</li>
  <li><svg width="11" height="11" viewBox="0 0 12 12"><circle cx="6" cy="6" r="6" fill="#fff"/><path d="M3 6l2 2 4-4" fill="none" stroke="#f78f20" stroke-width="1.6"/></svg>HEAVY DOMESTIC DRIVEWAYS</li>
  <li><svg width="11" height="11" viewBox="0 0 12 12"><circle cx="6" cy="6" r="6" fill="#fff"/><path d="M3 6l2 2 4-4" fill="none" stroke="#f78f20" stroke-width="1.6"/></svg>COMMERCIAL PARKING</li>
  </ul><span class="btn more">&#9432; MORE INFO</span></div>
</article>

<article class="abs card" style="left:128px;top:1314px"><div class="photo" role="img" aria-label="White grid path laid in a garden" style="background:linear-gradient(180deg,#8fa87a,#d8dce0 45%,#b7bcc2)"></div><h4>PARKING AND PATH</h4><small>WAY SYSTEM</small><span class="btn">&#9432; MORE INFO</span></article>
<article class="abs card" style="left:372px;top:1314px"><div class="photo" role="img" aria-label="Close-up of loose gravel stones" style="background:linear-gradient(160deg,#b9ad98,#8c8070)"></div><h4>LIGHT DOMESTIC</h4><small>DRIVEWAYS</small><span class="btn">&#9432; MORE INFO</span></article>
<article class="abs card" style="left:616px;top:1314px"><div class="photo" role="img" aria-label="Digger preparing ground for a driveway" style="background:linear-gradient(180deg,#7a8f66,#9a7b62 55%,#4f7a62)"></div><h4>HEAVY DOMESTIC</h4><small>DRIVEWAYS</small><span class="btn">&#9432; MORE INFO</span></article>
<article class="abs card" style="left:855px;top:1314px"><div class="photo" role="img" aria-label="Workers laying grid panels for a car park" style="background:linear-gradient(180deg,#a9b8c6,#b7ab94 50%,#6f6a62)"></div><h4>COMMERCIAL PARKING</h4><small>WAY SYSTEM</small><span class="btn">&#9432; MORE INFO</span></article>

<article class="abs card" style="left:128px;top:1599px"><div class="photo" role="img" aria-label="Steel pins laid over green grid" style="background:linear-gradient(135deg,#4e7a3a,#a4b39a 50%,#3d5f2e)"></div><h4>STEEL U PINS</h4><small>WAY SYSTEM</small><span class="btn">&#9432; MORE INFO</span></article>
<article class="abs card" style="left:372px;top:1599px"><div class="photo" role="img" aria-label="Black honeycomb grid laid across a field" style="background:linear-gradient(180deg,#8fb0d0,#5c7a4c 30%,#3a3a3a 60%,#1e1e1e)"></div><h4>TERRALOCK GRID</h4><small>WAY SYSTEM</small><span class="btn">&#9432; MORE INFO</span></article>
<article class="abs card" style="left:616px;top:1599px"><div class="photo" role="img" aria-label="Plants above curved garden edging" style="background:linear-gradient(180deg,#4c7a32,#7a9a52 45%,#a38b6c)"></div><h4>GARDEN EDGING</h4><small>WAY SYSTEM</small><span class="btn">&#9432; MORE INFO</span></article>
<article class="abs card" style="left:855px;top:1599px"><div class="photo" role="img" aria-label="Grass growing through a reinforcement grid" style="background:linear-gradient(180deg,#2d2d2d,#4f7a3a 40%,#6f9a4e 75%,#2e2e2e)"></div><h4>GRASS REINFORCEMENT</h4><small>WAY SYSTEM</small><span class="btn">&#9432; MORE INFO</span></article>

<section class="abs cta" role="img" aria-label="Dark close-up of gravel in a hexagonal grid"></section>
<p class="abs cta-q">NEED HELP / ADVICE OR WANT A QUOTE?</p>
<p class="abs cta-call">CALL US ON: <span>0138-000-5566</span></p>
<span class="abs btn cta-btn">&#9432; MORE INFO</span>

<footer class="abs footer"></footer>
<h3 class="abs footer-title" style="left:100px;top:2260px">CONTACT INFO</h3>
<div class="f-row" style="left:100px;top:2302px"><svg width="12" height="16" viewBox="0 0 12 16"><path d="M6 0a6 6 0 0 0-6 6c0 4.5 6 10 6 10s6-5.5 6-10a6 6 0 0 0-6-6zm0 8.5A2.5 2.5 0 1 1 6 3.5a2.5 2.5 0 0 1 0 5z" fill="#fff"/></svg><span>PonderMesh eco solutions<br>Riverside House,Millbrook Ind Est,<br>Ashford Vale, AV1 2XY.</span></div>
<div class="f-row" style="left:100px;top:2376px;font-size:16px;color:#fff"><svg width="14" height="14" viewBox="0 0 24 24"><path fill="#fff" d="M6.6 10.8a15 15 0 0 0 6.6 6.6l2.2-2.2c.3-.3.7-.4 1-.2 1.1.4 2.3.6 3.6.6.6 0 1 .4 1 1V20c0 .6-.4 1-1 1A17 17 0 0 1 3 4c0-.6.4-1 1-1h3.5c.6 0 1 .4 1 1 0 1.3.2 2.5.6 3.6.1.3 0 .7-.2 1z"/></svg>0845-000-1234</div>
<div class="f-row" style="left:100px;top:2418px"><svg width="16" height="12" viewBox="0 0 16 12" style="margin-top:4px"><rect x=".5" y=".5" width="15" height="11" fill="none" stroke="#fff"/><path d="M.5.5L8 7l7.5-6.5" fill="none" stroke="#fff"/></svg>sales@pondermeshpaths.co.uk</div>
<h3 class="abs footer-title" style="left:455px;top:2260px">NEWSLETTER</h3>
<div class="field" style="top:2305px">Enter your name...</div>
<div class="field" style="top:2352px">Email address...</div>
<span class="abs btn submit">Submit</span>
<svg class="abs" style="left:904px;top:2264px" width="50" height="54" viewBox="0 0 50 54"><path d="M25 1l23 13v26L25 53 2 40V14z" fill="none" stroke="#aaa" stroke-width="1.5"/></svg>
<p class="abs tweet"><a>http://www.pondermeshpaths.co.uk/latest_tweet_<br>item latest_tweetitem</a><br><em>4 min ago</em></p>
<div class="abs bottom"><p>Copyright 2016 pondermeshpaths. All Rights Reserved</p>
<div class="social"><i style="background:var(--blue)"></i><i style="background:var(--sky)"></i><i style="background:var(--navy)"></i><i style="background:var(--orange)"></i></div>
<span class="code">C12</span></div>
</body>
</html>
```